Creating a Label for the Wine "Kemora"

Kemora
As you know Kemora is an imagined place or state of things in which everything is perfect. This wine reflects that. It is a high value wine and it is perfect. The dimensions shoulb be between 9c x 11,5 cm and 12cm x 8 cm

```html
<!DOCTYPE html>
<html lang="en">
<head>
<meta charset="utf-8">
<title>Kemora — Red Wine Label</title>
<link rel="stylesheet" href="https://fonts.googleapis.com/css2?family=Cinzel:wght@400;500&family=Cormorant+Garamond:wght@500&display=swap">
<style>
  :root {
    --backdrop-top: #2a2a2a;
    --backdrop-bottom: #121212;
    --label-edge: #0b0b0b;
    --parchment-light: #ecd3a2;
    --parchment-mid: #dcb87e;
    --parchment-dark: #b88f55;
    --ink: #2b2622;
    --wine-red: #a3162a;
  }
  * { margin: 0; padding: 0; box-sizing: border-box; }
  html, body {
    width: 1200px;
    height: 3023px;
    overflow: hidden;
  }
  body {
    background: linear-gradient(180deg, var(--backdrop-top) 0%, var(--backdrop-bottom) 100%);
    position: relative;
  }
  .wine-label {
    position: absolute;
    left: 150px;
    top: 940px;
    width: 900px;
    height: 1140px;
    background: var(--label-edge);
  }
  .parchment {
    position: absolute;
    inset: 24px 18px;
    display: block;
  }
  .label-content {
    position: absolute;
    inset: 0;
    display: flex;
    flex-direction: column;
    align-items: center;
  }
  .brand-dot {
    position: absolute;
    top: 330px;
    width: 54px;
    height: 54px;
    border-radius: 50%;
    background: var(--wine-red);
  }
  .brand-name {
    position: absolute;
    top: 520px;
    font-family: "Cinzel", "Times New Roman", serif;
    font-weight: 400;
    font-size: 138px;
    letter-spacing: 2px;
    color: var(--ink);
    line-height: 1;
  }
  .wine-type {
    position: absolute;
    top: 920px;
    font-family: "Cormorant Garamond", "Times New Roman", serif;
    font-weight: 500;
    font-size: 34px;
    letter-spacing: 3px;
    color: var(--ink);
    text-transform: uppercase;
  }
</style>
</head>
<body>
  <section class="wine-label">
    <svg class="parchment" viewBox="0 0 864 1092" width="864" height="1092" preserveAspectRatio="none" role="img" aria-label="Aged parchment scroll with rolled top and bottom edges">
      <defs>
        <radialGradient id="parchmentTone" cx="50%" cy="50%" r="70%">
          <stop offset="0%" stop-color="var(--parchment-light)"/>
          <stop offset="70%" stop-color="var(--parchment-mid)"/>
          <stop offset="100%" stop-color="var(--parchment-dark)"/>
        </radialGradient>
      </defs>
      <rect x="0" y="0" width="864" height="1092" fill="url(#parchmentTone)"/>
    </svg>
    <div class="label-content">
      <span class="brand-dot"></span>
      <h1 class="brand-name">KEMORA</h1>
      <p class="wine-type">Red Wine</p>
    </div>
  </section>
</body>
</html>
```